Brightwave Reach - Business Card

We need a business card for a Social Media Marketing company that specializes in online marketing for small businesses in Canada using common Social Media platforms such as Pixlora, Chatterly, Blinkpost & Quibber.

I have uploaded a copy of our logo which I would like utilized in the business card. We would like the business card to be modern yet classy design.

Our website is www.brightwavereach.ca

Industry/Entity Type

Marketing

Contact Information for Business Card

Email: info@brightwavereach.ca
Website: www.brightwavereach.ca
Telephone: 604-555-0193

Colors

Designer to choose colors to be used in the design.

Requirements
Must have
• Social Media icons on reverse
• Please add some designs with color.

```html
<!DOCTYPE html>
<html lang="en">
<head>
<meta charset="utf-8">
<title>Brightwave Reach – Business Card</title>
<link href="https://fonts.googleapis.com/css2?family=Lato:wght@400;700;900&display=swap" rel="stylesheet">
<style>
  :root {
    --ink: #111111;
    --charcoal: #3a3c3e;
    --band: #4a4c4f;
    --paper: #ffffff;
    --stage: #d9dadb;
    --muted: #2b2b2b;
  }
  * { box-sizing: border-box; margin: 0; padding: 0; }
  html, body { width: 1200px; height: 900px; overflow: hidden; }
  body {
    background: var(--stage);
    font-family: "Lato", sans-serif;
    display: flex;
    flex-direction: column;
    align-items: center;
    justify-content: center;
    gap: 36px;
  }
  .card {
    position: relative;
    width: 700px;
    height: 400px;
    overflow: hidden;
    box-shadow: 0 6px 18px rgba(0,0,0,0.25);
  }

  /* Brand lockup: plain square + name */
  .brand {
    position: absolute;
    display: flex;
    align-items: center;
    gap: 16px;
  }
  .brand-mark { flex: none; }
  .brand-name {
    font-weight: 900;
    text-transform: uppercase;
    line-height: 1;
    letter-spacing: 1px;
    white-space: nowrap;
  }

  /* Reverse side */
  .card-back { background: var(--ink); color: var(--paper); }
  .card-back .brand {
    left: 50%; top: 95px;
    transform: translateX(-50%);
  }
  .card-back .brand-mark { width: 34px; height: 34px; background: var(--paper); }
  .card-back .brand-name { font-size: 38px; color: var(--paper); }
  .social-row {
    position: absolute;
    left: 0; right: 0; bottom: 70px;
    display: flex; justify-content: center; gap: 90px;
    list-style: none;
  }
  .social-square {
    display: block;
    width: 46px; height: 46px;
    background: var(--paper);
    border-radius: 9px;
  }

  /* Front side */
  .card-front { background: var(--paper); color: var(--muted); }
  .card-front .brand { left: 40px; top: 60px; }
  .card-front .brand-mark { width: 30px; height: 30px; background: var(--charcoal); }
  .card-front .brand-name { font-size: 32px; color: var(--charcoal); }
  .contact {
    position: absolute;
    left: 40px; top: 200px;
    list-style: none;
    font-size: 17px;
    color: var(--muted);
  }
  .contact li { display: flex; align-items: center; gap: 12px; margin-bottom: 6px; }
  .contact svg { width: 15px; height: 15px; fill: var(--charcoal); }
  .person {
    position: absolute;
    right: 110px; top: 200px;
  }
  .person-name { font-size: 28px; font-weight: 700; color: var(--muted); }
  .person-role { font-size: 18px; font-weight: 400; color: var(--muted); }
  .swoosh { position: absolute; left: 0; top: 0; width: 700px; height: 400px; }
  .website {
    position: absolute;
    right: 40px; bottom: 14px;
    font-size: 19px;
    color: var(--paper);
    letter-spacing: 0.5px;
  }
</style>
</head>
<body>

  <section class="card card-back" aria-label="Card reverse">
    <div class="brand"><span class="brand-mark"></span><span class="brand-name">Brightwave<br>Reach</span></div>
    <ul class="social-row" aria-label="Chatterly, Pixlora, Quibber, Blinkpost">
      <li><span class="social-square"></span></li>
      <li><span class="social-square"></span></li>
      <li><span class="social-square"></span></li>
      <li><span class="social-square"></span></li>
    </ul>
  </section>

  <section class="card card-front" aria-label="Card front">
    <svg class="swoosh" viewBox="0 0 700 400" aria-hidden="true">
      <path d="M0,255 C220,275 460,330 700,300 L700,400 L0,400 Z" fill="#4a4c4f"/>
      <path d="M0,270 C220,292 460,350 700,322 L700,400 L0,400 Z" fill="#ffffff"/>
      <path d="M0,278 C220,302 460,362 700,334 L700,400 L0,400 Z" fill="#111111"/>
    </svg>

    <div class="brand"><span class="brand-mark"></span><span class="brand-name">Brightwave<br>Reach</span></div>

    <ul class="contact">
      <li>
        <svg viewBox="0 0 24 24" aria-hidden="true"><path d="M6.6 10.8a15.1 15.1 0 0 0 6.6 6.6l2.2-2.2a1 1 0 0 1 1-.25 11.4 11.4 0 0 0 3.6.57 1 1 0 0 1 1 1V20a1 1 0 0 1-1 1A17 17 0 0 1 3 4a1 1 0 0 1 1-1h3.5a1 1 0 0 1 1 1c0 1.250.2 2.45.57 3.57a1 1 0 0 1-.25 1z"/></svg>
        604-555-0193
      </li>
      <li>
        <svg viewBox="0 0 24 24" aria-hidden="true"><path d="M2 5h20v14H2z M2 5l10 8 10-8" fill="none" stroke="#3a3c3e" stroke-width="2"/></svg>
        info@brightwavereach.ca
      </li>
    </ul>

    <div class="person">
      <p class="person-name">Daniel Ferris</p>
      <p class="person-role">Manager</p>
    </div>

    <p class="website">www.brightwavereach.ca</p>
  </section>

</body>
</html>
```